Cat-products company needs smart, yet endearing, business card

We need a business card design for a new, but up-and-running, business based in Honolulu, Hawaii. The business is Purrnest Nook Co. Our first product is the most environmentally-friendly cat grass kit ever seen on the planet. Future products, currently in the R&D phase, will include a variety of exciting cat scratchers. We also do consulting work to help apartment-dwellers make their home more cat-friendly and, in the future, plan on doing full, custom installs of structure to create high walkways for cats.

Target Market(s)

Middle-aged, apartment-dwelling, middle-class workers who own 1 or more cats and who dote on them.

Industry/Entity Type

Pet Care

Contact Information for Business Card

A striking, professional, yet warm and friendly design is what we're after.

Font styles to use
Serif
Sans Serif
Other font styles liked:
• Comfortaa

Colors

Designer to choose colors to be used in the design.

Requirements
Must have
• The company logo: (see attachment)
• The company name: Purrnest Nook Co
• The web address: www.purrnestnookco.com
• Email: support@purrnestnookco.com
• Phone: +1 (808) 571 6023
• Update (Fri Jun 30 3017 7:45pm Hawaii Time) I would like, is possible, uploaded picture of the cat grass kit on the back of the card with some text along the lines of: Purrnest Nook Co - Maker Of The Leafiest Feline Sprout Set Yet
Nice to have
• A cat picture, cartoon, real or silhouette that illustrates cats in action and/or relaxing; ie using the apartment space to live, play and relax in and being well-contented.
• Most of the website is done in the font: Comfortaa. It might be nice to continue using this for brand consistency.
Should not have
• Hard-to-read fonts.

```html
<!DOCTYPE html>
<html lang="en">
<head>
<meta charset="utf-8">
<title>Purrnest Nook Co – Business Card</title>
<link rel="stylesheet" href="https://fonts.googleapis.com/css2?family=Questrial&family=Roboto+Condensed:wght@500&family=Varela+Round&display=swap">
<style>
  :root {
    --backdrop: #e4e4e4;
    --card-white: #f7f7f7;
    --brown: #512f2a;
    --yellow: #f2ac00;
    --ink: #4a4a4a;
    --rule: #6b6b6b;
    --white: #ffffff;
  }
  * { margin: 0; padding: 0; box-sizing: border-box; }
  html, body { width: 1200px; height: 960px; overflow: hidden; }
  body { background: var(--backdrop); position: relative; font-family: "Questrial", sans-serif; }

  .card { position: absolute; width: 600px; height: 342px; border-radius: 18px; overflow: hidden; }

  /* Front */
  .card-front { left: 314px; top: 113px; background: var(--card-white); }
  .card-front .base-band { position: absolute; left: 0; right: 0; bottom: 0; height: 12px; background: var(--brown); border-top: 4px solid var(--yellow); }

  .brand-mark { position: absolute; right: 34px; top: 118px; display: flex; align-items: center; gap: 10px; }
  .brand-mark .dot { width: 26px; height: 26px; border-radius: 50%; background: var(--brown); }
  .brand-name { font-family: "Varela Round", sans-serif; color: var(--yellow); font-size: 28px; line-height: 1; }

  .holder { position: absolute; left: 33px; top: 189px; }
  .holder-name { font-family: "Roboto Condensed", sans-serif; font-weight: 500; font-size: 23px; color: var(--brown); line-height: 1; letter-spacing: .2px; }
  .holder-role { font-size: 15px; color: var(--yellow); margin-top: 8px; letter-spacing: .3px; }

  .divider { position: absolute; left: 33px; right: 33px; top: 243px; height: 1px; background: var(--rule); }

  .contact-list { position: absolute; left: 33px; top: 256px; list-style: none; }
  .contact-list li { display: flex; align-items: center; gap: 9px; font-size: 15px; color: var(--ink); height: 19.5px; }
  .contact-list svg { width: 12px; height: 12px; fill: var(--ink); flex: none; }

  .social-row { position: absolute; right: 32px; top: 254px; display: flex; gap: 2px; }
  .social-row span { width: 20px; height: 20px; border-radius: 50%; background: var(--brown); }
  .social-row span:nth-child(even) { background: var(--yellow); }

  .address { position: absolute; right: 32px; top: 277px; text-align: right; font-size: 15px; color: var(--ink); line-height: 19.5px; }

  /* Back */
  .card-back { left: 311px; top: 472px; background: var(--brown); }
  .emblem-area { position: absolute; left: 14px; top: 14px; width: 314px; height: 314px; border-radius: 50%; background: var(--yellow); }
  .back-brand { position: absolute; right: 45px; top: 200px; text-align: right; }
  .back-brand .brand-name { display: block; font-size: 40px; line-height: 1.05; }
  .back-url { position: absolute; right: 30px; top: 300px; font-size: 14px; color: var(--white); letter-spacing: 2.2px; }
</style>
</head>
<body>

<section class="card card-front" aria-label="Business card front">
  <div class="brand-mark">
    <span class="dot"></span>
    <span class="brand-name">Purrnest Nook Co</span>
  </div>

  <div class="holder">
    <p class="holder-name">LEILANI KAHALE</p>
    <p class="holder-role">CEO/FOUNDER</p>
  </div>

  <div class="divider"></div>

  <ul class="contact-list">
    <li>
      <svg viewBox="0 0 24 24" aria-hidden="true"><path d="M6.6 10.8a15.2 15.2 0 0 0 6.6 6.6l2.2-2.2c.3-.3.7-.4 1-.2 1.1.4 2.3.6 3.6.6.6 0 1 .4 1 1V20c0 .6-.4 1-1 1A17 17 0 0 1 3 4c0-.6.4-1 1-1h3.5c.6 0 1 .4 1 1 0 1.3.2 2.5.6 3.6.1.3 0 .7-.2 1z"/></svg>
      +1 (808) 571 6023
    </li>
    <li>
      <svg viewBox="0 0 24 24" aria-hidden="true"><path d="M2 5h20v14H2z"/><path d="M3 6.5l9 7 9-7V6H3z" fill="#f7f7f7"/></svg>
      support@purrnestnookco.com
    </li>
    <li>
      <svg viewBox="0 0 24 24" aria-hidden="true"><circle cx="12" cy="12" r="11"/><path d="M12 1v22M1 12h22" stroke="#f7f7f7" stroke-width="1.6" fill="none"/><ellipse cx="12" cy="12" rx="5" ry="11" stroke="#f7f7f7" stroke-width="1.6" fill="none"/></svg>
      www.purrnestnookco.com
    </li>
  </ul>

  <div class="social-row" aria-hidden="true"><span></span><span></span><span></span><span></span></div>

  <p class="address">4120 Hibiscus Way<br>Honolulu, Hawaii 96815</p>

  <div class="base-band"></div>
</section>

<section class="card card-back" aria-label="Business card back">
  <div class="emblem-area" role="img" aria-label="Large brand emblem area"></div>
  <div class="back-brand">
    <span class="brand-name">Purrnest</span>
    <span class="brand-name">Nook Co</span>
  </div>
  <p class="back-url">www.purrnestnookco.com</p>
</section>

</body>
</html>
```